New LLC consulting company needs a business card design

I need a business card design for new company in Alexandria Virginia called TK Verdane Consulting LLC. The company is focused on consulting for defense and national security issues with expertise in nuclear and space topics. I would like to see designs that are simple and I am open to colors except for brown.

Target Market(s)

All businesses that are seeking consulting help

Industry/Entity Type

Consulting

Contact Information for Business Card

Name of company - TK Verdane Consulting LLC; name (Delia Pratt) President; email: prattdq47@mailvessa.com; Phone: 703-555-0142

Requirements
Must have
• The details described above
Nice to have
• I'm open to all ideas
Should not have
• No brown

```html
<!DOCTYPE html>
<html lang="en">
<head>
<meta charset="utf-8">
<title>TK Verdane Consulting LLC — Business Card</title>
<link href="https://fonts.googleapis.com/css2?family=Poppins:wght@400;500;600&display=swap" rel="stylesheet">
<style>
  :root {
    --bg: #f0f0f0;
    --card: #ffffff;
    --ink: #111111;
    --blue: #1a73bb;
    --rule: #222222;
  }
  * { margin: 0; padding: 0; box-sizing: border-box; }
  html, body {
    width: 1200px; height: 987px; overflow: hidden;
    background: var(--bg);
    font-family: "Poppins", sans-serif;
    color: var(--ink);
  }
  .card {
    position: absolute;
    left: 245px;
    width: 710px; height: 405px;
    background: var(--card);
    border-radius: 34px;
  }
  .card--front { top: 68px; }
  .card--back { top: 514px; }

  .wordmark {
    position: absolute;
    display: flex; align-items: center;
    font-weight: 600;
    color: var(--ink);
    white-space: nowrap;
    transform: translate(-50%, -50%);
  }
  .wordmark__dot {
    flex: none;
    border-radius: 50%;
    background: var(--blue);
  }
  .card--front .wordmark { left: 355px; top: 200px; font-size: 36px; gap: 14px; }
  .card--front .wordmark__dot { width: 22px; height: 22px; }
  .card--back .wordmark { left: 168px; top: 202px; font-size: 19px; gap: 8px; }
  .card--back .wordmark__dot { width: 12px; height: 12px; }

  .divider {
    position: absolute;
    left: 356px; top: 98px;
    width: 1px; height: 206px;
    background: var(--rule);
  }

  .contact { position: absolute; left: 417px; top: 120px; }
  .contact__name {
    font-size: 34px; line-height: 1; color: var(--blue); font-weight: 400;
    letter-spacing: 0.3px;
  }
  .contact__name strong { font-weight: 600; }
  .contact__title { font-size: 18px; font-weight: 500; margin-top: 6px; line-height: 1; }
  .contact__list { list-style: none; margin-top: 28px; }
  .contact__item {
    display: flex; align-items: center; gap: 10px;
    font-size: 17px; line-height: 24px; letter-spacing: 0.4px;
  }
  .contact__item svg { width: 16px; height: 16px; flex: none; }
</style>
</head>
<body>
  <section class="card card--front" aria-label="Card front">
    <div class="wordmark"><span class="wordmark__dot"></span>TK Verdane Consulting LLC</div>
  </section>

  <section class="card card--back" aria-label="Card back">
    <div class="wordmark"><span class="wordmark__dot"></span>TK Verdane Consulting LLC</div>
    <div class="divider"></div>
    <div class="contact">
      <h1 class="contact__name"><strong>Delia</strong> Pratt</h1>
      <p class="contact__title">President</p>
      <ul class="contact__list">
        <li class="contact__item">
          <svg viewBox="0 0 24 24" aria-hidden="true"><path fill="#1a73bb" d="M6.6 10.8a15.1 15.1 0 0 0 6.6 6.6l2.2-2.2a1 1 0 0 1 1-.25 11.4 11.4 0 0 0 3.6.57 1 1 0 0 1 1 1V20a1 1 0 0 1-1 1A17 17 0 0 1 3 4a1 1 0 0 1 1-1h3.5a1 1 0 0 1 1 1c0 1.25.2 2.45.57 3.57a1 1 0 0 1-.25 1z"/><path fill="none" stroke="#1a73bb" stroke-width="1.8" d="M14 3a7 7 0 0 1 7 7M14 6.5a3.5 3.5 0 0 1 3.5 3.5"/></svg>
          703-555-0142
        </li>
        <li class="contact__item">
          <svg viewBox="0 0 24 24" aria-hidden="true"><path fill="#1a73bb" d="M2 9l10-7 10 7v12H2z"/><path fill="#fff" d="M5 8h14v7l-7 4-7-4z"/><circle cx="12" cy="11" r="2.2" fill="none" stroke="#1a73bb" stroke-width="1.3"/><path fill="none" stroke="#fff" stroke-width="1.2" d="M2 21l8-6M22 21l-8-6"/></svg>
          prattdq47@mailvessa.com
        </li>
      </ul>
    </div>
  </section>
</body>
</html>
```